Indy Film Production Company/Studio

We need a business card designed from an existing logo. We are a digital studio/production company that caters to creating genre entertainment, like Action, Horror, and martial arts. The card along with the logo will be used to Brand the company from letter heads to banners. The design will also be used for postcards and Brochures. It should be professional and masculine.
Updates

Thank you to all the designers who have participated. I'm narrowing down who it will be. Thank you again.

Target Market(s)

Investors, Networks, Producers, and actors

Industry/Entity Type

Film Production

Contact Information for Business Card

Teodoro Valbuena
Producer/Writer/Director
www.kestrelpicturehouse.example

Requirements
Must have
• Website address, Facebook icon and Twitter icon possibly in the back of the card.
Nice to have
• Logline of Company: Follow The Action.

```html
<!DOCTYPE html>
<html lang="en">
<head>
<meta charset="utf-8">
<title>Kestrel Picture House – Business Card</title>
<link href="https://fonts.googleapis.com/css2?family=Montserrat:wght@400;500;700;800&display=swap" rel="stylesheet">
<style>
  :root {
    --backdrop: #2b2b2b;
    --paper: #ffffff;
    --ink: #111111;
    --ink-soft: #444444;
    --accent: #e8232a;
  }
  * { box-sizing: border-box; margin: 0; padding: 0; }
  html, body {
    width: 1200px; height: 900px; overflow: hidden;
    background: var(--backdrop);
    font-family: "Montserrat", sans-serif;
  }
  .stage { position: relative; width: 1200px; height: 900px; }
  .card {
    position: absolute; left: 250px; width: 700px; height: 400px;
    background: var(--paper);
    overflow: hidden;
  }
  .card--front { top: 40px; }
  .card--back { top: 470px; }

  .stripes { position: absolute; left: 0; right: 0; bottom: 0; }
  .stripes .rule { height: 3px; background: var(--ink); }
  .stripes .gap { height: 6px; background: var(--paper); }
  .stripes .band {
    height: 38px; background: var(--accent);
    display: flex; align-items: center; justify-content: center;
  }
  .stripes .base { height: 14px; background: var(--paper); }
  .stripes .band .web {
    color: var(--paper); font-size: 17px; font-weight: 400; letter-spacing: 0.5px;
  }

  .wordmark {
    font-weight: 800; color: var(--ink); text-transform: uppercase;
    line-height: 1.02; letter-spacing: 1px;
  }
  .card--front .wordmark {
    position: absolute; left: 0; right: 0; top: 120px;
    text-align: center; font-size: 46px;
  }
  .card--back .wordmark {
    position: absolute; right: 40px; top: 95px;
    text-align: right; font-size: 28px;
  }

  .contact { position: absolute; left: 50px; top: 150px; width: 340px; }
  .contact .name {
    font-size: 22px; font-weight: 700; color: var(--ink);
    text-transform: uppercase; letter-spacing: 1px; white-space: nowrap;
  }
  .contact .role {
    font-size: 12px; font-weight: 500; color: var(--ink-soft);
    text-transform: uppercase; letter-spacing: 1px; margin-top: 3px;
    white-space: nowrap;
  }
  .contact ul { list-style: none; margin-top: 14px; }
  .contact li {
    display: flex; align-items: center; gap: 10px;
    font-size: 14px; color: var(--ink-soft); line-height: 22px; white-space: nowrap;
  }
  .contact li svg { width: 12px; height: 12px; flex: none; }
  .contact .social { display: flex; gap: 8px; margin-top: 12px; }
  .contact .social span {
    width: 22px; height: 22px; border-radius: 50%; background: var(--ink);
  }
</style>
</head>
<body>
<div class="stage">

  <section class="card card--front">
    <div class="wordmark">Kestrel<br>Picture House</div>
    <div class="stripes">
      <div class="rule"></div>
      <div class="band"><span class="web">www.kestrelpicturehouse.example</span></div>
      <div class="rule"></div>
      <div class="gap"></div>
      <div class="rule"></div>
      <div class="base"></div>
    </div>
  </section>

  <section class="card card--back">
    <div class="wordmark">Kestrel<br>Picture House</div>
    <div class="contact">
      <div class="name">Teodoro Valbuena</div>
      <div class="role">Producer / Writer / Director</div>
      <ul>
        <li>
          <svg viewBox="0 0 24 24" fill="#222"><path d="M6.6 10.8a15 15 0 0 0 6.6 6.6l2.2-2.2a1 1 0 0 1 1-.25 11.4 11.4 0 0 0 3.6.57 1 1 0 0 1 1 1V20a1 1 0 0 1-1 1A17 17 0 0 1 3 4a1 1 0 0 1 1-1h3.5a1 1 0 0 1 1 1c0 1.25.2 2.45.57 3.57a1 1 0 0 1-.25 1z"/></svg>
          +330 2460-7183
        </li>
        <li>
          <svg viewBox="0 0 24 24" fill="none" stroke="#222" stroke-width="2"><rect x="3" y="5" width="18" height="14" rx="1"/><path d="M3 6l9 7 9-7"/></svg>
          info@kestrelpicturehouse.example
        </li>
        <li>
          <svg viewBox="0 0 24 24" fill="none" stroke="#222" stroke-width="2"><circle cx="12" cy="12" r="9"/><path d="M3 12h18M12 3c3 3 3 15 0 18M12 3c-3 3-3 15 0 18"/></svg>
          www.kestrelpicturehouse.example
        </li>
      </ul>
      <div class="social">
        <span role="img" aria-label="Social profile link"></span>
        <span role="img" aria-label="Social profile link"></span>
      </div>
    </div>
    <div class="stripes">
      <div class="rule"></div>
      <div class="band"></div>
      <div class="rule"></div>
      <div class="gap"></div>
      <div class="rule"></div>
      <div class="base"></div>
    </div>
  </section>

</div>
</body>
</html>
```